Four in One (Flexible infographic for Content Management Industry)

See attachment.
A graphic depicting 4 products, where each can stand on its own and each can be combined with others, but where, if all are taken together, the best result is achieved (the "super product").
Intended use is web. See attached file as an example.
The most basic idea is as the attached diagram shows, where 4 rectangles are arranged in a quadrangle, with a middle rectangle in the center representing the combined 4 products. This concept is fine except it is a bit too obvious as it stands. We are looking for either a variation of this or another concept.
The audience is technical + professional + enterprise - NOT consumers. Hence the design should be conservative in nature.
We are aware of tools like as Canva or Pictogram where such graphics are available, but we are looking for something with a bit more imagination and flexibility.
This graphic should be targeted to web sites and be delivered with vector-based (SVG) graphics.

```html
<!DOCTYPE html>
<html lang="en">
<head>
<meta charset="utf-8">
<title>Four in One – Super Product</title>
<link rel="stylesheet" href="https://fonts.googleapis.com/css2?family=Poppins:wght@400;500;600;700&family=Open+Sans:wght@700;800&display=swap">
<style>
  :root {
    --green: #8cbf4a;
    --blue: #1a6fc0;
    --teal: #1f9aa6;
    --purple: #8e2a8e;
    --ink: #2f2f2f;
    --body: #3a3a3a;
    --navy: #1c2340;
    --hub: #f8f6f7;
    --paper: #ffffff;
  }
  * { box-sizing: border-box; margin: 0; padding: 0; }
  html, body { width: 1200px; height: 878px; overflow: hidden; background: var(--paper); }
  .canvas { position: relative; width: 1200px; height: 878px; font-family: "Poppins", sans-serif; color: var(--body); }
  .frame { position: absolute; inset: 0; }

  .module { position: absolute; }
  .module h2 { font-weight: 700; font-size: 23px; line-height: 1.05; letter-spacing: 0.2px; }
  .module p { font-size: 12.6px; line-height: 1.22; margin-top: 8px; }
  .features { list-style: none; margin-top: 16px; }
  .features li { position: relative; font-weight: 600; font-size: 12.8px; line-height: 1.2; height: 23.7px; padding-left: 15px; color: var(--ink); }
  .tick { position: absolute; left: 0; top: 4px; width: 9px; height: 9px; border-radius: 50%; border: 1px solid var(--accent); opacity: .85; }
  .tick::after { content: ""; position: absolute; left: 2px; top: 0.5px; width: 2.5px; height: 4.5px; border: solid var(--accent); border-width: 0 1.2px 1.2px 0; transform: rotate(45deg); }
  .learn-more { display: block; font-weight: 500; font-size: 13.4px; color: #222; margin-top: 16px; text-decoration: none; }

  .module--documents { left: 185px; top: 124px; width: 330px; --accent: var(--green); }
  .module--documents h2 { color: var(--green); }
  .module--security { left: 690px; top: 124px; width: 340px; --accent: var(--blue); }
  .module--security h2 { color: var(--blue); }
  .module--security p { color: var(--navy); }
  .module--security .features { padding-left: 74px; }
  .module--security .features li { color: var(--navy); }
  .module--security .learn-more { margin-left: 74px; }
  .module--erp { left: 181px; top: 497px; width: 290px; --accent: var(--teal); }
  .module--erp h2 { color: var(--teal); }
  .module--erp p { width: 250px; margin-top: 6px; }
  .module--erp .features { margin-top: 6px; }
  .module--erp .learn-more { margin-top: 10px; }
  .module--digital { left: 781px; top: 497px; width: 290px; --accent: var(--purple); }
  .module--digital h2 { color: var(--purple); font-size: 24px; }
  .module--digital p { width: 250px; margin-top: 4px; }
  .module--digital .features { margin-left: -7px; margin-top: 14px; }
  .module--digital .features li { color: var(--navy); }
  .module--digital .learn-more { margin-top: 16px; }

  .hub-label { position: absolute; left: 455px; top: 390px; width: 300px; text-align: center;
    font-family: "Open Sans", sans-serif; font-weight: 800; font-size: 39px; line-height: 1.02; color: var(--ink); letter-spacing: 0.5px; }
</style>
</head>
<body>
<main class="canvas">
  <svg class="frame" width="1200" height="878" viewBox="0 0 1200 878" aria-hidden="true">
    <defs>
      <radialGradient id="hub-fill" cx="50%" cy="45%" r="55%">
        <stop offset="0" stop-color="#fbfafb"/>
        <stop offset="1" stop-color="#f3f1f2"/>
      </radialGradient>
      <filter id="hub-shadow" x="-20%" y="-20%" width="140%" height="140%">
        <feDropShadow dx="0" dy="2" stdDeviation="4" flood-color="#000" flood-opacity=".28"/>
      </filter>
    </defs>
    <g fill="none" stroke-width="4" stroke-linecap="round">
      <path class="outline outline--documents" stroke="var(--green)" d="M435,397 H141 A26,26 0 0 1 115,371 V133 A26,26 0 0 1 141,107 H537 A26,26 0 0 1 563,133 V259"/>
      <path class="outline outline--security" stroke="var(--blue)" d="M641,259 V133 A26,26 0 0 1 667,107 H1062 A26,26 0 0 1 1088,133 V371 A26,26 0 0 1 1062,397 H774"/>
      <path class="outline outline--erp" stroke="var(--teal)" d="M435,477 H141 A26,26 0 0 0 115,503 V741 A26,26 0 0 0 141,767 H537 A26,26 0 0 0 563,741 V614"/>
      <path class="outline outline--digital" stroke="var(--purple)" d="M774,477 H1062 A26,26 0 0 1 1088,503 V741 A26,26 0 0 1 1062,767 H667 A26,26 0 0 1 641,741 V614"/>
    </g>
    <g class="hub-arcs" fill="none" stroke-width="5">
      <path stroke="var(--green)" d="M446,421 A160,160 0 0 1 591,276"/>
      <path stroke="var(--blue)" d="M619,276 A160,160 0 0 1 764,421"/>
      <path stroke="var(--purple)" d="M764,449 A160,160 0 0 1 619,594"/>
      <path stroke="var(--teal)" d="M591,594 A160,160 0 0 1 446,449"/>
    </g>
    <circle class="hub" cx="605" cy="435" r="136" fill="url(#hub-fill)" stroke="#d8d6d7" stroke-width="3" filter="url(#hub-shadow)"/>

    <g class="badge badge--documents" transform="translate(106,108)">
      <circle r="64" fill="#fff" stroke="var(--green)" stroke-width="3"/>
      <circle r="55" fill="#f2f2f2" stroke="var(--green)" stroke-width="7"/>
      <rect x="-20" y="-24" width="26" height="30" fill="#e6e6e6" stroke="#bbb"/>
      <path d="M-28,-14 H-12 L-8,-10 H20 V22 H-28 Z" fill="#f7c81e"/>
      <circle cx="17" cy="18" r="10" fill="#333"/>
      <circle cx="17" cy="18" r="4" fill="#f2f2f2"/>
    </g>
    <g class="badge badge--security" transform="translate(1105,108)">
      <circle r="64" fill="#fff" stroke="var(--blue)" stroke-width="3"/>
      <circle r="55" fill="#f2f2f2" stroke="var(--blue)" stroke-width="7"/>
      <rect x="-22" y="-30" width="30" height="36" fill="#e6e6e6" stroke="#bbb"/>
      <rect x="-24" y="-12" width="44" height="34" rx="3" fill="#f7c81e"/>
      <path d="M2,-2 L18,4 V16 C18,26 10,31 2,34 C-6,31 -14,26 -14,16 V4 Z" fill="#3a8ee6"/>
      <rect x="-4" y="11" width="12" height="10" rx="1.5" fill="#e63946"/>
      <path d="M-1,11 V7 A3,3 0 0 1 5,7 V11" fill="none" stroke="#e63946" stroke-width="2"/>
    </g>
    <g class="badge badge--erp" transform="translate(106,776)">
      <circle r="64" fill="#fff" stroke="var(--teal)" stroke-width="3"/>
      <circle r="55" fill="#f2f2f2" stroke="var(--teal)" stroke-width="7"/>
      <circle r="26" fill="none" stroke="#2477d6" stroke-width="11" stroke-dasharray="9 4.6"/>
      <circle r="22" fill="#2f8ae6"/>
      <circle r="13" fill="#e8f1fb"/>
      <circle cy="-4" r="5" fill="#f5a04a"/>
      <path d="M-9,9 A9,8 0 0 1 9,9 Z" fill="#f5a04a"/>
    </g>
    <g class="badge badge--digital" transform="translate(1105,776)">
      <circle r="64" fill="#fff" stroke="var(--purple)" stroke-width="3"/>
      <circle r="55" fill="#f2f2f2" stroke="var(--purple)" stroke-width="7"/>
      <g fill="none" stroke="#2a86e0" stroke-width="3">
        <path d="M-24,-14 V-24 H-14 M14,-24 H24 V-14 M24,14 V24 H14 M-14,24 H-24 V14"/>
      </g>
      <g stroke="#8a8a8a" stroke-width="2">
        <path d="M-10,-14 H10 M-10,-7 H10 M-10,7 H10 M-10,14 H4"/>
      </g>
      <path d="M-24,0 H24" stroke="#2a86e0" stroke-width="3"/>
    </g>
  </svg>

  <section class="module module--documents">
    <h2>Document Management</h2>
    <p>Streamline document organization, access, and collaboration with easier file storage and sharing, leading to more efficient workflows.</p>
    <ul class="features">
      <li><span class="tick"></span>Centralized Document Control</li>
      <li><span class="tick"></span>Collaborative Workspace Integration</li>
      <li><span class="tick"></span>Automated Compliance Tracking</li>
      <li><span class="tick"></span>Check 4</li>
    </ul>
    <a class="learn-more" href="#">Learn More</a>
  </section>

  <section class="module module--security">
    <h2>Security and Compliance</h2>
    <p>Benefit from tailored cloud solutions, secure data storage, and expert disaster recovery planning for reliable and scalable IT operations.</p>
    <ul class="features">
      <li><span class="tick"></span>Custom Cloud Solutions</li>
      <li><span class="tick"></span>Secure Data Storage</li>
      <li><span class="tick"></span>Expert Disaster Recovery</li>
      <li><span class="tick"></span>Check 4</li>
    </ul>
    <a class="learn-more" href="#">Learn More</a>
  </section>

  <section class="module module--erp">
    <h2>Enterprise<br>Resource Planning</h2>
    <p>Streamline document organization, access, and collaboration with easier file storage and sharing, leading to more efficient workflows.</p>
    <ul class="features">
      <li><span class="tick"></span>Centralized Document Control</li>
      <li><span class="tick"></span>Collaborative Workspace Integration</li>
      <li><span class="tick"></span>Automated Compliance Tracking</li>
      <li><span class="tick"></span>Check 4</li>
    </ul>
    <a class="learn-more" href="#">Learn More</a>
  </section>

  <section class="module module--digital">
    <h2>Digitital<br>Transformation</h2>
    <p>Turn scanned documents into easily searchable digital archives, boosting efficiency and accessibility.</p>
    <ul class="features">
      <li><span class="tick"></span>Instant searchable Archives with OCR</li>
      <li><span class="tick"></span>Automated Document Classification</li>
      <li><span class="tick"></span>TeamVault and Cloud Blob Ready</li>
      <li><span class="tick"></span>Check 4</li>
    </ul>
    <a class="learn-more" href="#">Learn More</a>
  </section>

  <h1 class="hub-label">SUPER<br>PRODUCT</h1>
</main>
</body>
</html>
```